Award-winnning Estate Agent needs a premium version of their 'For Sale' board design

We need a premium option for our 'For Sale' board design. We have a standard board that is attached to this brief, but were are looking to have a premium design version that we will use when selling exclusive properties. Our company name is Harbourline Vale Estates and the name for this is exclusive selection is: 'The Harbourline Collection'. The design needs to work with our current brand, but have a distinctive PREMIUM feel to it. I have uploaded the barnd guidelines and also some of the exisisting logo variations. We do NOT need a new logo but feel free to play around with colours, fonts, sizes etc. for the sign.

Target Market(s)

Property buyers & house hunters

Industry/Entity Type

Real Estate - Residential Property

Font styles to use
Sans Serif

Requirements
Must have
• A premium fee, must be square design, must be easy to read when driving past the sign
Nice to have
• I'm open ot ideas

```html
<!DOCTYPE html>
<html lang="en">
<head>
<meta charset="utf-8">
<title>Harbourline Vale Estates – For Sale Board</title>
<link rel="stylesheet" href="https://fonts.googleapis.com/css2?family=Archivo:wdth,wght@100..125,500..900&display=swap">
<style>
  :root {
    --brand-navy: #2d3790;
    --brand-blue: #1b77ba;
    --brand-sky: #27a8e0;
    --paper: #ffffff;
  }
  html, body {
    margin: 0;
    padding: 0;
    width: 1200px;
    height: 1200px;
    overflow: hidden;
    background: var(--paper);
  }
  .board {
    display: block;
    width: 1200px;
    height: 1200px;
  }
  .brand-name {
    font-family: "Archivo", Arial, sans-serif;
    font-weight: 600;
    font-stretch: 100%;
    fill: var(--brand-navy);
  }
  .collection-title {
    font-family: "Archivo", "Arial Black", sans-serif;
    font-weight: 900;
    font-stretch: 125%;
    fill: var(--brand-blue);
  }
  .headline {
    font-family: "Archivo", "Arial Black", sans-serif;
    font-weight: 900;
    font-stretch: 125%;
  }
  .headline-for { fill: var(--brand-navy); }
  .headline-sale { fill: var(--paper); }
  .phone-number, .web-address {
    font-family: "Archivo", "Arial Black", sans-serif;
    font-weight: 900;
    font-stretch: 115%;
    fill: var(--paper);
  }
  .fill-navy { fill: var(--brand-navy); }
  .fill-blue { fill: var(--brand-blue); }
  .fill-sky { fill: var(--brand-sky); }
  .fill-paper { fill: var(--paper); }
</style>
</head>
<body>
<svg class="board" viewBox="0 0 1200 1200" xmlns="http://www.w3.org/2000/svg">
  <defs>
    <linearGradient id="skyline-tone" x1="0" y1="0" x2="0" y2="1">
      <stop offset="0" stop-color="#2d3790"/>
      <stop offset="0.35" stop-color="#1b77ba"/>
      <stop offset="0.7" stop-color="#27a8e0"/>
      <stop offset="1" stop-color="#1b77ba"/>
    </linearGradient>
    <linearGradient id="skyline-row-tone" x1="0" y1="0" x2="1" y2="0">
      <stop offset="0" stop-color="#1b77ba"/>
      <stop offset="0.5" stop-color="#27a8e0"/>
      <stop offset="1" stop-color="#1b77ba"/>
    </linearGradient>
  </defs>

  <!-- Brand lockup -->
  <g class="brand">
    <rect class="fill-blue" x="179" y="146" width="86" height="86"/>
    <text class="brand-name" x="290" y="184" font-size="44">Harbourline Vale</text>
    <text class="brand-name" x="290" y="230" font-size="44">Estates</text>
  </g>

  <!-- Corner accent -->
  <polygon class="fill-blue corner-accent" points="713.5,104 1032,104 1032,315.5"/>

  <!-- Collection title -->
  <text class="collection-title" x="292" y="391" font-size="40"
        textLength="621" lengthAdjust="spacingAndGlyphs">THE HARBOURLINE COLLECTION</text>

  <!-- Headline -->
  <text class="headline headline-for" x="292" y="524" font-size="120"
        textLength="250" lengthAdjust="spacingAndGlyphs">FOR</text>
  <rect class="fill-sky sale-panel" x="564" y="408" width="350.5" height="143"/>
  <text class="headline headline-sale" x="582" y="524" font-size="120"
        textLength="317" lengthAdjust="spacingAndGlyphs">SALE</text>

  <!-- Phone band -->
  <rect class="fill-blue phone-band" x="168" y="664" width="612" height="95"/>
  <circle class="fill-paper" cx="239" cy="667" r="41"/>
  <circle class="fill-navy" cx="239" cy="667" r="35"/>
  <path class="fill-paper phone-icon"
        d="M224.5 647.5 c3 -3 7 -2 9 1 l5 7 c2 3 1 6 -2 8 c-2 1 -2 3 0 6 c3 5 7 9 12 12 c3 2 5 2 6 0 c2 -3 5 -4 8 -2 l7 5 c3 2 3 6 0 9 c-4 4 -10 5 -17 1 c-10 -5 -19 -14 -25 -25 c-5 -8 -7 -17 -3 -22 z"/>
  <text class="phone-number" x="318" y="736" font-size="56"
        textLength="422" lengthAdjust="spacingAndGlyphs">01632 960418</text>

  <rect x="785" y="581" width="247" height="178" fill="url(#skyline-tone)"
        role="img" aria-label="Stylised town skyline with clock tower and rooftops"/>
  <rect class="fill-paper" x="785" y="681" width="247" height="4"/>

  <!-- Web band -->
  <rect class="fill-navy web-band" x="168" y="765" width="864" height="210"/>
  <text class="web-address" x="237" y="831" font-size="42"
        textLength="726" lengthAdjust="spacingAndGlyphs">www.harbourlinevaleestates.co.uk</text>

  <rect class="fill-paper" x="168" y="896" width="864" height="4"/>
  <rect x="168" y="900" width="864" height="75" fill="url(#skyline-row-tone)"
        role="img" aria-label="Repeating row of stylised town skylines with clock towers"/>
</svg>
</body>
</html>
```